We are a new company with 2 divisions a medical research and medical product sales. We need a company logo and Business Cards. The design files need to be provided to us in Adobe Photoshop CS 5.1.

Target Market(s)

Medical Community

Industry/Entity Type

Medical

Contact Information for Business Card

Company Name - Harrowgate Lifesciences LLC
Company Address 4127 Larkspur Ave Suite 7, Marlow Springs Fl 32614

Requirements
Must have
• The design files need to be provided to us in Adobe Photoshop CS 5.1.

```html
<!DOCTYPE html>
<html lang="en">
<head>
<meta charset="utf-8">
<title>Harrowgate Lifesciences LLC – Business Card</title>
<link rel="stylesheet" href="https://fonts.googleapis.com/css2?family=Sorts+Mill+Goudy&display=swap">
<style>
  :root {
    --page-bg: #e9e6e1;
    --card-paper: #f3f4f6;
    --brand-blue: #1f3f88;
    --band-blue: #1d3c86;
    --band-blue-deep: #122c6a;
    --ink-dark: #2a2a2e;
    --ink-cream: #dccdaa;
    --ink-rust: #b27a62;
  }
  * { margin: 0; padding: 0; box-sizing: border-box; }
  html, body {
    width: 1200px;
    height: 970px;
    overflow: hidden;
    background: var(--page-bg);
  }
  .canvas {
    position: relative;
    width: 1200px;
    height: 970px;
  }
  .business-card {
    position: absolute;
    left: 100px;
    top: 215px;
    width: 1000px;
    height: 540px;
    background: var(--card-paper);
    box-shadow: 0 10px 30px rgba(0,0,0,0.18);
    font-family: "Sorts Mill Goudy", serif;
    overflow: hidden;
  }
  .brand {
    position: absolute;
    left: 38px;
    top: 22px;
    display: flex;
    align-items: center;
    gap: 16px;
  }
  .brand-mark {
    width: 159px;
    height: 159px;
    flex: none;
  }
  .brand-name {
    color: var(--brand-blue);
    font-size: 52px;
    font-weight: 400;
    line-height: 56px;
    letter-spacing: 0.5px;
    text-transform: uppercase;
  }
  .person {
    position: absolute;
    right: 62px;
    top: 220px;
    text-align: right;
    color: var(--ink-dark);
  }
  .person-name {
    font-size: 42px;
    line-height: 44px;
  }
  .person-title {
    font-size: 30px;
    line-height: 34px;
  }
  .contact-band {
    position: absolute;
    left: 0;
    bottom: 0;
    width: 100%;
    height: 226px;
    background: linear-gradient(100deg, var(--band-blue) 0%, var(--band-blue) 55%, var(--band-blue-deep) 100%);
  }
  .contact-list {
    position: absolute;
    left: 50px;
    top: 16px;
    list-style: none;
    font-size: 28px;
    line-height: 32px;
  }
  .contact-list .address { color: var(--ink-cream); }
  .contact-list .reach { color: var(--ink-rust); }
</style>
</head>
<body>
<main class="canvas">
  <section class="business-card">
    <header class="brand">
      <svg class="brand-mark" viewBox="0 0 160 160" aria-hidden="true">
        <circle cx="80" cy="80" r="76" fill="var(--brand-blue)"/>
      </svg>
      <h1 class="brand-name">Harrowgate<br>Lifesciences LLC.</h1>
    </header>

    <div class="person">
      <p class="person-name">John Doe</p>
      <p class="person-title">Chief Executive Officer</p>
    </div>

    <div class="contact-band">
      <ul class="contact-list">
        <li class="address">4127 Larkspur Avenue</li>
        <li class="address">Suite 7,</li>
        <li class="address">Marlow Springs Fl 32614</li>
        <li class="reach">Phone: 123 456 789</li>
        <li class="reach">Email: yourname@yourcompany.com</li>
        <li class="reach">www.yourcompany.com</li>
      </ul>
    </div>
  </section>
</main>
</body>
</html>
```